Veltrona Pocket Folder

Create a new pocket folder
An Overview / Background of the Business & Services
We would like a new folder to use when making formal presentations
* The Target Market / Audience you are trying to reach
The target audience are commercial businesses that we are selling group insurance products to
* Design Specifics; any preferences or ideas for Style, Colour, Imagery, etc
We wanted to use the Houston, Texas skyline and create something that was simple, yet modern.
* Do you have an existing website or Facebook page were designers can learn more about your company?
Yes, http://www.veltronagroup.example and we are on Linked-In.
Updates
Project Deadline Extended Reason: We have many people who have to agree. We need to get an answer on the form of the ready art we will receive when we select a designer .Thank you. Added Thursday, April 27, 2017
Industry/Entity Type
Business
Look and feel
Each slider illustrates characteristics of the customer's brand and the style your logo design should communicate.

```html
<!DOCTYPE html>
<html lang="en">
<head>
<meta charset="utf-8">
<title>Veltrona Pocket Folder</title>
<link rel="stylesheet" href="https://fonts.googleapis.com/css2?family=Open+Sans:wght@400;700&family=Roboto:wght@700&display=swap">
<style>
  :root {
    --stage: #c4c4c4;
    --charcoal: #56565a;
    --charcoal-dark: #3f3f43;
    --brand-blue: #1a8fd0;
    --brand-blue-deep: #0b5f98;
    --paper: #ffffff;
    --paper-shade: #ececec;
    --sky-grey: #cfd1d3;
    --sky-blue: #d6e3ea;
    --ink: #5a5a5e;
    --contact: #d8d8da;
  }
  * { margin: 0; padding: 0; box-sizing: border-box; }
  html, body { width: 1200px; height: 828px; overflow: hidden; }
  body { background: var(--stage); position: relative; font-family: "Open Sans", sans-serif; }

  .folder-spread {
    position: absolute; left: 70px; top: 64px;
    width: 1060px; height: 700px;
    display: flex;
    box-shadow: 0 18px 40px rgba(0,0,0,.25);
  }
  .back-cover, .front-cover { position: relative; width: 530px; height: 700px; overflow: hidden; }

  .back-cover .cover-art { position: absolute; inset: 0; }

  .contact-block {
    position: absolute; left: 44px; bottom: 60px;
    color: var(--contact); font-size: 10px; line-height: 1.45;
  }
  .contact-block .company { font-weight: 700; }
  .contact-list { list-style: none; margin-top: 10px; }
  .contact-list li { display: flex; align-items: center; gap: 8px; }
  .contact-list svg { width: 9px; height: 9px; fill: var(--contact); }

  .front-cover { background: linear-gradient(160deg, var(--paper) 0%, var(--paper) 55%, var(--paper-shade) 100%); }
  .wordmark {
    position: absolute; left: 92px; top: 104px;
    display: flex; align-items: center; gap: 10px;
  }
  .wordmark-square { width: 52px; height: 44px; background: var(--brand-blue); border-radius: 4px; }
  .wordmark-name {
    font-family: "Roboto", sans-serif; font-weight: 700;
    font-size: 40px; color: var(--ink); letter-spacing: .5px;
  }
  .skyline {
    position: absolute; left: 0; right: 0; bottom: 0; height: 330px;
    background: linear-gradient(90deg, var(--sky-grey) 0%, var(--sky-blue) 35%, var(--sky-grey) 70%, #c2c4c6 100%);
    opacity: .85;
  }
</style>
</head>
<body>
  <main class="folder-spread">
    <section class="back-cover">
      <svg class="cover-art" viewBox="0 0 530 700" preserveAspectRatio="none" aria-hidden="true">
        <defs>
          <linearGradient id="charcoal-fill" x1="0" y1="0" x2="1" y2="1">
            <stop offset="0" stop-color="#5e5e62"/>
            <stop offset="1" stop-color="#3f3f43"/>
          </linearGradient>
          <radialGradient id="blue-fill" cx="0.35" cy="0.3" r="0.8">
            <stop offset="0" stop-color="#1a9ad8"/>
            <stop offset="1" stop-color="#0b5f98"/>
          </radialGradient>
          <linearGradient id="band-fill" x1="0" y1="0" x2="1" y2="0">
            <stop offset="0" stop-color="#d9d9d9"/>
            <stop offset="0.5" stop-color="#ffffff"/>
            <stop offset="1" stop-color="#cfcfcf"/>
          </linearGradient>
        </defs>
        <rect class="base" width="530" height="700" fill="url(#charcoal-fill)"/>
        <path class="band" d="M60,0 C110,260 300,520 530,640 L530,700 L500,700 C300,600 60,380 0,120 L0,0 Z" fill="url(#band-fill)"/>
        <path class="blue-field" d="M120,0 L530,0 L530,560 C330,470 170,280 120,0 Z" fill="url(#blue-fill)"/>
      </svg>
      <address class="contact-block">
        <div class="company">Veltrona Agency LLC</div>
        <div>4820 North Alder Row, Suite 210</div>
        <div>Houston, Texas, 77001</div>
        <ul class="contact-list">
          <li><svg viewBox="0 0 10 10"><path d="M2 0h2l1 3-1.5 1a6 6 0 0 0 2.5 2.5L7 5l3 1v2c0 1-1 2-2 2A8 8 0 0 1 0 2c0-1 1-2 2-2z"/></svg>713-555-0142</li>
          <li><svg viewBox="0 0 10 10"><path d="M0 2h10v6H0z M0 2l5 3.5L10 2" fill="none" stroke="#d8d8da" stroke-width="1.2"/></svg>info@veltronagroup.example</li>
          <li><svg viewBox="0 0 10 10"><circle cx="5" cy="5" r="4.4" fill="none" stroke="#d8d8da" stroke-width="1.1"/><path d="M.6 5h8.8M5 .6v8.8" stroke="#d8d8da" stroke-width="1"/></svg>www.veltronagroup.example</li>
        </ul>
      </address>
    </section>

    <section class="front-cover">
      <div class="wordmark">
        <span class="wordmark-square"></span>
        <span class="wordmark-name">Veltrona</span>
      </div>
      <div class="skyline" role="img" aria-label="Faint silhouette of the Houston, Texas city skyline"></div>
    </section>
  </main>
</body>
</html>
```